KLV Plant Services

We are a heavy diesel mechanical business with additional air con certificates, remapping engine rebuilt

Contact Information for Business Card

Company Name, Director Name, Managing Director, Contact details, email and website

Font styles to use
Serif
Script

```html
<!DOCTYPE html>
<html lang="en">
<head>
<meta charset="utf-8">
<title>KLV Plant Services – Business Card</title>
<link rel="stylesheet" href="https://fonts.googleapis.com/css2?family=Roboto:wght@400;700&display=swap">
<style>
  :root {
    --navy: #02035f;
    --paper: #f3f3f4;
    --ink: #000000;
    --stage: #d9d9d9;
    --white: #ffffff;
    --faint-mark: #3b3fb4;
  }
  * { box-sizing: border-box; margin: 0; padding: 0; }
  html, body {
    width: 1200px; height: 1040px; overflow: hidden;
    background: var(--stage);
    font-family: "Roboto", Arial, sans-serif;
  }
  .card {
    position: absolute; left: 278px;
    width: 644px; height: 366px;
    border-radius: 18px; overflow: hidden;
    background: var(--navy);
  }
  .card--front { top: 130px; }
  .card--back { top: 567px; }
  .front-panel { position: absolute; inset: 0; }
  .holder {
    position: absolute; left: 32px; top: 76px; color: var(--white);
  }
  .holder__name { font-size: 25px; font-weight: 700; line-height: 1.1; }
  .holder__title { font-size: 16.5px; font-weight: 400; margin-top: 2px; margin-left: 2px; }
  .address {
    position: absolute; left: 32px; top: 173px; color: var(--white);
    font-size: 16.5px; line-height: 20px;
  }
  .contacts {
    position: absolute; left: 32px; top: 228px; list-style: none; color: var(--white);
    font-size: 16.5px; line-height: 20px;
  }
  .contacts li { display: flex; align-items: center; gap: 8px; }
  .contacts svg { width: 13px; height: 13px; fill: var(--white); flex: none; }
  .wordmark {
    position: absolute; left: 380px; top: 150px; width: 200px;
    display: flex; align-items: center; gap: 10px;
    color: var(--navy); font-weight: 700; line-height: 1;
  }
  .wordmark__dot {
    width: 20px; height: 20px; border-radius: 50%; background: var(--navy); flex: none;
  }
  .wordmark__main { display: block; font-size: 46px; letter-spacing: 1px; }
  .wordmark__sub { display: block; font-size: 16px; margin-top: 4px; }
  .wordmark--faint {
    left: 0; right: 0; top: 120px; width: auto; justify-content: center;
    color: var(--faint-mark); gap: 16px;
  }
  .wordmark--faint .wordmark__dot { width: 28px; height: 28px; background: var(--faint-mark); }
  .wordmark--faint .wordmark__main { font-size: 76px; }
  .wordmark--faint .wordmark__sub { font-size: 26px; margin-top: 6px; }
  .back-web {
    position: absolute; left: 0; right: 0; top: 324px; text-align: center;
    color: var(--white); font-size: 16px; letter-spacing: 3.5px;
  }
</style>
</head>
<body>
  <section class="card card--front" aria-label="Business card front">
    <svg class="front-panel" viewBox="0 0 644 366" aria-hidden="true">
      <polygon fill="var(--paper)" points="424,0 644,0 644,366 424,366 245,183"/>
      <polygon fill="var(--ink)" points="424,0 434,0 272,183 434,366 424,366 259,183"/>
    </svg>
    <div class="holder">
      <p class="holder__name">Owen Hartley</p>
      <p class="holder__title">Managing Director</p>
    </div>
    <p class="address">4172 Harbour Lane<br>Riverton, NY 11420</p>
    <ul class="contacts">
      <li><svg viewBox="0 0 16 16"><path d="M3.5 1l2.6 3.2-1.5 1.9c.9 2 2.4 3.5 4.4 4.4l1.9-1.5L14 11.6 12.6 15C6.5 14.6 1.4 9.5 1 3.4z"/></svg>(555) 0142-7786</li>
      <li><svg viewBox="0 0 16 16"><path d="M1 3h14v10H1zm1.5 1.5v.4L8 8.6l5.5-3.7v-.4zm0 2.2v4.8h11V6.7L8 10.4z"/></svg>name@KLV.com</li>
      <li><svg viewBox="0 0 16 16"><path d="M8 1a7 7 0 100 14A7 7 0 008 1zm-1 2.2c-.4 1 .2 1.6-.7 2.3-.8.6-2.2.2-2.4 1.3-.2 1 1.2 1.4 1.6 2.3.4.9-.3 2.4.6 3.3a5.2 5.2 0 01-3-7.9c1.1-.9 2.5-1.1 3.9-1.3zm3 1c.8.7.4 1.8 1.4 2.2.8.3 1.6-.1 1.8.8a5.2 5.2 0 01-3 5.7c-.2-1.2.7-2.1.2-3.1-.5-1-2-.6-2.3-1.8-.3-1.3 1.2-2.4 1.9-3.8z"/></svg>www.KLV.com</li>
    </ul>
    <div class="wordmark">
      <span class="wordmark__dot"></span>
      <span><span class="wordmark__main">KLV</span><span class="wordmark__sub">Plant Services</span></span>
    </div>
  </section>

  <section class="card card--back" aria-label="Business card back">
    <div class="wordmark wordmark--faint">
      <span class="wordmark__dot"></span>
      <span><span class="wordmark__main">KLV</span><span class="wordmark__sub">Plant Services</span></span>
    </div>
    <p class="back-web">www.KLV.com</p>
  </section>
</body>
</html>
```